Business Card Design Project

Business card based on attached logo

Todd Merrick
Todd@lorvantest.com
877-514-9073 ext. 318
Www.LorvanTest.com

Industry/Entity Type

Business

```html
<!DOCTYPE html>
<html lang="en">
<head>
<meta charset="utf-8">
<title>LorvanTest Business Cards</title>
<link rel="stylesheet" href="https://fonts.googleapis.com/css2?family=Arimo:wght@400;700&display=swap">
<style>
  :root {
    --brand-red: #e31b25;
    --ink: #231f20;
    --paper: #ffffff;
    --backdrop: #e9e7e4;
    --muted: #5a5657;
  }
  * { margin: 0; padding: 0; box-sizing: border-box; }
  html, body {
    width: 1200px;
    height: 715px;
    overflow: hidden;
  }
  body {
    background: var(--backdrop);
    font-family: "Arimo", Arial, sans-serif;
    position: relative;
  }
  .card {
    position: absolute;
    width: 505px;
    height: 288px;
    overflow: hidden;
    box-shadow: 0 2px 6px rgba(0,0,0,0.18);
  }
  .card--front   { left: 55px;  top: 42px;  background: var(--paper); }
  .card--white   { left: 623px; top: 37px;  background: var(--paper); }
  .card--red     { left: 51px;  top: 378px; background: var(--brand-red); }
  .card--black   { left: 629px; top: 381px; background: var(--ink); }

  /* Wordmark */
  .wordmark {
    position: absolute;
    left: 0; right: 0;
    display: flex;
    justify-content: center;
    align-items: center;
    gap: 12px;
    font-weight: 700;
    letter-spacing: -1px;
    line-height: 1;
  }
  .wordmark__square {
    width: 0.42em;
    height: 0.42em;
    background: var(--brand-red);
    flex: none;
  }
  .card--front .wordmark { top: 46px; font-size: 54px; color: var(--ink); }
  .card--white .wordmark,
  .card--red .wordmark,
  .card--black .wordmark { top: 92px; font-size: 58px; }
  .card--white .wordmark { color: var(--brand-red); }
  .card--red .wordmark   { color: var(--paper); }
  .card--black .wordmark { color: var(--paper); }
  .card--red .wordmark__square,
  .card--black .wordmark__square { background: var(--paper); }

  /* Front details */
  .holder-name {
    position: absolute;
    left: 86px;
    top: 196px;
    font-size: 20px;
    letter-spacing: 0.5px;
    color: var(--brand-red);
  }
  .divider {
    position: absolute;
    left: 234px;
    top: 172px;
    width: 1px;
    height: 70px;
    background: linear-gradient(to bottom, transparent, #8a8586 20%, #8a8586 80%, transparent);
  }
  .contact-list {
    position: absolute;
    left: 254px;
    top: 174px;
    list-style: none;
    font-size: 14px;
    color: var(--ink);
  }
  .contact-list li {
    display: flex;
    align-items: center;
    gap: 6px;
    height: 24px;
  }
  .contact-list svg { width: 11px; height: 11px; flex: none; }
  .front-wave {
    position: absolute;
    left: 0; bottom: 0;
    width: 505px;
    height: 288px;
  }

  /* Web address */
  .web-address {
    position: absolute;
    left: 0; right: 0;
    bottom: 18px;
    text-align: center;
    font-size: 15.5px;
    letter-spacing: 3px;
  }
  .card--white .web-address { color: var(--ink); }
  .card--red .web-address,
  .card--black .web-address { color: var(--paper); }
</style>
</head>
<body>

  <section class="card card--front" aria-label="Business card front">
    <svg class="front-wave" viewBox="0 0 543 309" preserveAspectRatio="none" aria-hidden="true">
      <path d="M0,266 C130,306 320,292 543,262 L543,309 L0,309 Z" fill="var(--brand-red)"/>
      <path d="M0,256 C130,300 320,284 543,256 C320,290 130,304 0,263 Z" fill="var(--ink)"/>
    </svg>

    <div class="wordmark">
      <span>LorvanTest</span>
      <span class="wordmark__square"></span>
    </div>

    <p class="holder-name">Todd Merrick</p>
    <div class="divider"></div>

    <ul class="contact-list">
      <li>
        <svg viewBox="0 0 12 12" aria-hidden="true">
          <circle cx="6" cy="6" r="5.3" fill="none" stroke="var(--brand-red)" stroke-width="1.2"/>
          <path d="M4.2,3.2 L5.2,3.2 L5.5,4.6 L4.9,5.1 C5.3,6 6,6.7 6.9,7.1 L7.4,6.5 L8.8,6.8 L8.8,7.8 C6.2,8 4,5.8 4.2,3.2 Z" fill="var(--brand-red)"/>
        </svg>
        <span>877-514-9073 ext. 318</span>
      </li>
      <li>
        <svg viewBox="0 0 12 12" aria-hidden="true">
          <rect x="1" y="3" width="10" height="7" rx="1" fill="var(--brand-red)"/>
          <path d="M1.5,3.6 L6,7 L10.5,3.6" fill="none" stroke="#fff" stroke-width="1"/>
        </svg>
        <span>Todd@lorvantest.com</span>
      </li>
      <li>
        <svg viewBox="0 0 12 12" aria-hidden="true">
          <circle cx="6" cy="6" r="5" fill="none" stroke="var(--brand-red)" stroke-width="1.1"/>
          <ellipse cx="6" cy="6" rx="2.2" ry="5" fill="none" stroke="var(--brand-red)" stroke-width="1"/>
          <path d="M1,6 H11 M2,3.5 H10 M2,8.5 H10" stroke="var(--brand-red)" stroke-width="0.9"/>
        </svg>
        <span>www.LorvanTest.com</span>
      </li>
    </ul>
  </section>

  <section class="card card--white" aria-label="Business card back, white">
    <div class="wordmark">
      <span>LorvanTest</span>
      <span class="wordmark__square"></span>
    </div>
    <p class="web-address">www.LorvanTest.com</p>
  </section>

  <section class="card card--red" aria-label="Business card back, red">
    <div class="wordmark">
      <span>LorvanTest</span>
      <span class="wordmark__square"></span>
    </div>
    <p class="web-address">www.LorvanTest.com</p>
  </section>

  <section class="card card--black" aria-label="Business card back, black">
    <div class="wordmark">
      <span>LorvanTest</span>
      <span class="wordmark__square"></span>
    </div>
    <p class="web-address">www.LorvanTest.com</p>
  </section>

</body>
</html>
```